Local Flower Farm Needs Business Card Design

I need business cards designed for a flower farm based in Eudora, Kansas.
Business Info:
We are a local cut flower farm located in Eudora, Kansas, founded by Corinne Haldwick. What started as a passion for agriculture and search for more joy in daily life has blossomed into a small business dedicated to providing the community with beautiful, fresh, and sustainable flowers. We specialize in local, seasonal blooms, ensuring that every petal reflects the care and dedication we pour into our craft. Our mission is to deliver the highest quality flowers directly to our customers through local farmers markets and to florists who share our commitment to sustainability. Join us in celebrating the beauty of nature, one bloom at a time!
Contact Details:
Corinne Haldwick
Owner
Phone 913-555-0147
Facebook: Rosalind Thorpe Gardens
Instagram: @RosalindThorpeGardens
Website: RosalindThorpeGardens.example
Target Market(s)
Wholesale to Florists and Direct to Consumer via Farmers Market
Industry/Entity Type
Florist, Farm
Contact Information for Business Card
Name, Contact Info, Logo
Look and feel
Each slider illustrates characteristics of the customer's brand and the style your logo design should communicate.

```html
<!DOCTYPE html>
<html lang="en">
<head>
<meta charset="utf-8">
<title>Rosalind Thorpe Gardens – Business Card</title>
<link rel="stylesheet" href="https://fonts.googleapis.com/css2?family=Playfair+Display:wght@400;700&family=Outfit:wght@300&display=swap">
<style>
  :root {
    --ink: #1d3336;
    --paper: #ffffff;
    --mist: #eef1f0;
    --leaf-light: #f3f5f4;
    --leaf-mid: #dde3e1;
    --backdrop: #9a9a9a;
  }
  * { margin: 0; padding: 0; box-sizing: border-box; }
  html, body { width: 1200px; height: 900px; overflow: hidden; }
  body {
    background: var(--backdrop);
    display: flex;
    flex-direction: column;
    align-items: center;
    justify-content: center;
    gap: 40px;
    font-family: "Outfit", sans-serif;
    color: var(--ink);
  }
  .card {
    position: relative;
    width: 640px;
    height: 366px;
    background: var(--paper);
    overflow: hidden;
  }
  .mist-shape {
    position: absolute;
    border-radius: 50%;
    background: var(--mist);
  }
  .mist-top-right { width: 190px; height: 190px; right: 50px; top: -90px; }
  .mist-bottom-left { width: 200px; height: 200px; left: 40px; bottom: -120px; }
  .foliage {
    position: absolute;
    background: linear-gradient(160deg, var(--leaf-light), var(--leaf-mid));
    border-radius: 60px;
    opacity: .85;
  }
  .front .foliage-left { left: 24px; top: 10px; width: 120px; height: 270px; }
  .front .foliage-right { right: 28px; top: 30px; width: 130px; height: 336px; border-radius: 60px 60px 0 0; }
  .back .foliage-right { right: 0; top: 110px; width: 150px; height: 256px; border-radius: 70px 0 0 0; }

  .front-emblem {
    position: absolute;
    left: 50%; top: 50%;
    width: 190px; height: 190px;
    transform: translate(-50%, -50%);
    border: 1.5px solid var(--ink);
    border-radius: 50%;
    display: flex;
    align-items: center;
    justify-content: center;
    text-align: center;
  }
  .brand-name {
    font-family: "Playfair Display", serif;
    font-weight: 400;
    color: var(--ink);
    line-height: 1.15;
  }
  .front-emblem .brand-name { font-size: 24px; }

  .rule { position: absolute; height: 1.5px; background: var(--ink); }
  .rule-lead { left: 0; top: 78px; width: 160px; }
  .rule-under { left: 400px; top: 106px; width: 190px; }
  .person-name {
    position: absolute;
    left: 172px; top: 56px;
    font-family: "Playfair Display", serif;
    font-weight: 700;
    font-size: 36px;
    letter-spacing: .5px;
  }
  .person-role {
    position: absolute;
    right: 50px; top: 112px;
    font-family: "Playfair Display", serif;
    font-size: 12px;
    letter-spacing: 2px;
  }
  .back-emblem {
    position: absolute;
    left: 56px; top: 168px;
    width: 132px; height: 132px;
    border: 1.5px solid var(--ink);
    display: flex;
    align-items: center;
    justify-content: center;
    text-align: center;
  }
  .back-emblem .brand-name { font-size: 19px; }
  .divider {
    position: absolute;
    left: 232px; top: 186px;
    width: 1.5px; height: 96px;
    background: var(--ink);
  }
  .contact-list {
    position: absolute;
    left: 256px; top: 178px;
    list-style: none;
    font-weight: 300;
    font-size: 15px;
  }
  .contact-list li {
    display: flex;
    align-items: center;
    gap: 9px;
    height: 26px;
  }
  .contact-icon { width: 13px; height: 13px; flex: none; }
</style>
</head>
<body>

  <section class="card front">
    <div class="mist-shape mist-top-right"></div>
    <div class="mist-shape mist-bottom-left"></div>
    <div class="foliage foliage-left" role="img" aria-label="Line-drawn leafy stem with ink speckles"></div>
    <div class="foliage foliage-right" role="img" aria-label="Line-drawn leafy stem rising from the bottom edge with ink speckles"></div>
    <div class="front-emblem">
      <p class="brand-name">Rosalind<br>Thorpe<br>Gardens</p>
    </div>
  </section>

  <section class="card back">
    <div class="foliage foliage-right" role="img" aria-label="Line-drawn leafy branch with ink speckles"></div>
    <div class="rule rule-lead"></div>
    <h1 class="person-name">Corinne Haldwick</h1>
    <div class="rule rule-under"></div>
    <p class="person-role">OWNER</p>

    <div class="back-emblem">
      <p class="brand-name">Rosalind<br>Thorpe<br>Gardens</p>
    </div>
    <div class="divider"></div>

    <ul class="contact-list">
      <li>
        <svg class="contact-icon" viewBox="0 0 24 24" fill="none" stroke="currentColor" stroke-width="1.8" stroke-linejoin="round" aria-hidden="true">
          <path d="M5 3h4l2 5-2.5 1.5a11 11 0 0 0 6 6L16 13l5 2v4a2 2 0 0 1-2 2A16 16 0 0 1 3 5a2 2 0 0 1 2-2z"/>
        </svg>
        913-555-0147
      </li>
      <li>
        <svg class="contact-icon" viewBox="0 0 24 24" fill="none" stroke="currentColor" stroke-width="1.8" aria-hidden="true"><circle cx="12" cy="12" r="8"/></svg>
        Rosalind Thorpe Gardens
      </li>
      <li>
        <svg class="contact-icon" viewBox="0 0 24 24" fill="none" stroke="currentColor" stroke-width="1.8" aria-hidden="true"><circle cx="12" cy="12" r="8"/></svg>
        @RosalindThorpeGardens
      </li>
      <li>
        <svg class="contact-icon" viewBox="0 0 24 24" fill="none" stroke="currentColor" stroke-width="1.6" aria-hidden="true">
          <circle cx="12" cy="12" r="9"/>
          <ellipse cx="12" cy="12" rx="4" ry="9"/>
          <path d="M3 12h18M5 7h14M5 17h14"/>
        </svg>
        RosalindThorpeGardens.example
      </li>
    </ul>
  </section>

</body>
</html>
```